Business card for Eyelash extension salon in Beverly Hills,California USA

We need new business card for our salon in Beverly Hills. The salon name is 'Lashvera' . We would like to have...Business name: Lashvera Name of person: will provide later Address 4720 N.Alder Crest Ave Beverly Hills , CA 90210 Phone: will provide later (Text only) Web: www.lashverastudio.example Snapgrid icon, Circlebook icon follow us for seasonal campaign and news @lashverastudiolounge Design should look elegant, high-end, clean, simple, cohesive with my brand. Please refer my brand board. Business name color will be metallic bronzy color. Im thinking grey background or white background. Thanks

Target Market(s)

25-35. Gender neutral. People who are in Entertainment business industry.
This is High-end Eyelash extension salon in Beverly Hills

Industry/Entity Type

Beauty Salon

Contact Information for Business Card

Business name: Lashvera
Name of person: will provide later
Address 4720 N.Alder Crest Ave Beverly Hills , CA 90210
Phone: will provide later (Text only)
Web: www.lashverastudio.example
Snapgrid icon, Circlebook icon
follow us for seasonal campaign and news @lashverastudiolounge

Requirements
Must have
• Beautiful, elegant, clean and simple look but very attractive and modern
Should not have
• We don't like too clutter, too busy designs.

```html
<!DOCTYPE html>
<html lang="en">
<head>
<meta charset="utf-8">
<title>Lashvera Beverly Hills – Business Card</title>
<link rel="stylesheet" href="https://fonts.googleapis.com/css2?family=Playfair+Display:wght@400;700&family=Josefin+Sans:wght@400&display=swap">
<style>
  :root {
    --bronze: #8b6549;
    --sand: #c8ab8e;
    --stone: #a9a7a8;
    --ink: #1f1f1f;
    --paper: #ffffff;
    --stage: #ffffff;
    --serif: "Playfair Display", Georgia, serif;
    --sans: "Josefin Sans", Arial, sans-serif;
  }
  * { box-sizing: border-box; margin: 0; padding: 0; }
  html, body {
    width: 1200px; height: 900px; overflow: hidden;
    background: var(--stage);
  }
  .stage { position: relative; width: 1200px; height: 900px; }

  .card {
    position: absolute;
    width: 642px; height: 367px;
    background: var(--paper);
    box-shadow: 12px 12px 10px rgba(0,0,0,0.55);
    overflow: hidden;
  }
  .card--front { left: 100px; top: 68px; }
  .card--back  { left: 415px; top: 483px; }

  /* Front */
  .front-wordmark {
    position: absolute; left: 0; width: 100%; top: 150px;
    text-align: center;
    font-family: var(--serif); font-weight: 400;
    font-size: 112px; line-height: 1;
    color: var(--bronze);
    letter-spacing: 1px;
  }
  .front-location {
    position: absolute; left: 314px; top: 288px;
    font-family: var(--sans); font-size: 17px;
    letter-spacing: 3.2px; color: var(--bronze);
  }

  /* Back */
  .holder-name {
    position: absolute; left: 37px; top: 38px;
    font-family: var(--serif); font-weight: 700;
    font-size: 40px; letter-spacing: 1px; color: var(--bronze);
  }
  .contact-list {
    position: absolute; left: 37px; top: 118px;
    list-style: none;
    font-family: var(--serif); font-size: 18.5px; color: var(--ink);
  }
  .contact-list li {
    display: flex; align-items: center; gap: 6px;
    height: 35px;
  }
  .contact-icon { width: 18px; height: 18px; flex: none; }
  .social-mark {
    width: 16px; height: 16px; flex: none;
    background: var(--bronze); margin: 0 1px;
  }
  .social-name { color: var(--bronze); margin-right: 4px; }

  .back-logo {
    position: absolute; right: 36px; top: 50px; width: 250px;
    text-align: center;
  }
  .back-wordmark {
    font-family: var(--serif); font-weight: 400;
    font-size: 54px; line-height: 1; color: var(--bronze);
  }
  .back-location {
    margin-top: 22px; padding-left: 80px;
    font-family: var(--sans); font-size: 9px;
    letter-spacing: 1.8px; color: var(--bronze);
  }

  .card-waves { position: absolute; left: 0; top: 0; width: 642px; height: 367px; }
  .website {
    position: absolute; right: 33px; top: 318px;
    font-family: var(--serif); font-size: 17px; color: var(--paper);
  }
</style>
</head>
<body>
<main class="stage">

  <section class="card card--front" aria-label="Card front">
    <div class="front-wordmark">Lashvera</div>
    <div class="front-location">BEVERLY HILLS</div>
  </section>

  <section class="card card--back" aria-label="Card back">
    <svg class="card-waves" viewBox="0 0 642 367" aria-hidden="true">
      <path fill="var(--stone)" d="M0 312 C70 332 210 334 330 322 C450 310 540 290 642 292 L642 367 L0 367 Z"/>
      <path fill="var(--sand)" d="M0 266 C110 282 260 291 416 289 C300 297 160 312 40 320 C20 318 6 314 0 310 Z"/>
    </svg>

    <h1 class="holder-name">NAME</h1>

    <ul class="contact-list">
      <li>
        <svg class="contact-icon" viewBox="0 0 18 18" aria-hidden="true">
          <path fill="var(--bronze)" d="M1 7 C1 3 17 3 17 7 L17 8 L13 8 L13 6 L5 6 L5 8 L1 8 Z"/>
          <path fill="var(--bronze)" d="M4 9 L14 9 L16 16 L2 16 Z"/>
          <circle cx="9" cy="12.5" r="2" fill="#fff"/>
        </svg>
        <span>123 456 789</span>
      </li>
      <li>
        <span class="social-mark" aria-hidden="true"></span>
        <span class="social-name">Circlebook</span>
        <span>@lashverastudiolounge</span>
      </li>
      <li>
        <span class="social-mark" aria-hidden="true"></span>
        <span class="social-name">Snapgrid</span>
        <span>@lashverastudiolounge</span>
      </li>
      <li>
        <svg class="contact-icon" viewBox="0 0 18 18" aria-hidden="true">
          <path fill="var(--bronze)" d="M9 1 C5.5 1 3 3.6 3 7 C3 11 9 17 9 17 C9 17 15 11 15 7 C15 3.6 12.5 1 9 1 Z"/>
          <circle cx="9" cy="7" r="2.3" fill="#fff"/>
        </svg>
        <span>4720 N.Alder Crest Ave Beverly Hills , CA 90210</span>
      </li>
    </ul>

    <div class="back-logo">
      <div class="back-wordmark">Lashvera</div>
      <div class="back-location">BEVERLY HILLS</div>
    </div>

    <div class="website">www.lashverastudio.example</div>
  </section>

</main>
</body>
</html>
```